Typography of the cover "Watch the tide turning"

We would like to improve the presentation of a book cover: presentation and typography of the authors and of the title. Image of the cover is available in two versions (with or without sky), joined with the texts (joined files): Mathis Corvenot Watched the turning tide Romance Editions Murlane

Industry/Entity Type

Publishing

Colors

Designer to choose colors to be used in the design.

Requirements
Must have
• Provided picture (with or without sky)

```html
<!DOCTYPE html>
<html lang="fr">
<head>
<meta charset="utf-8">
<title>Watch the tide turning — Mathis Corvenot</title>
<link rel="stylesheet" href="https://fonts.googleapis.com/css2?family=Josefin+Sans:wght@400&family=Libre+Bodoni:wght@400;500&display=swap">
<style>
  :root {
    --paper-top: #efefef;
    --paper-mid: #e2e2e2;
    --city-light: #c9c9c9;
    --city-mid: #8a8a8a;
    --city-dark: #3c3c3c;
    --ink: #161616;
    --title-red: #a3191c;
    --title-red-deep: #7e1012;
    --label-ink: #1c1c1c;
    --imprint: #f2f2f2;
  }
  * { margin: 0; padding: 0; box-sizing: border-box; }
  html, body { width: 810px; height: 1200px; overflow: hidden; }
  .cover {
    position: relative;
    width: 810px;
    height: 1200px;
    overflow: hidden;
    background: linear-gradient(180deg, var(--paper-top) 0%, var(--paper-mid) 45%, #d6d6d6 60%);
  }
  .cover__city {
    position: absolute;
    left: 0; right: 0;
    top: 470px; bottom: 0;
    background:
      linear-gradient(180deg, rgba(214,214,214,1) 0%, rgba(214,214,214,0) 28%),
      repeating-linear-gradient(90deg, rgba(255,255,255,0.10) 0 6px, rgba(0,0,0,0.08) 6px 14px, rgba(255,255,255,0.04) 14px 31px),
      linear-gradient(180deg, var(--city-light) 0%, var(--city-mid) 38%, var(--city-dark) 100%);
  }
  .cover__author {
    position: absolute;
    top: 22px; left: 0; right: 0;
    text-align: center;
    font-family: "Josefin Sans", sans-serif;
    font-size: 52px;
    letter-spacing: 2px;
    color: var(--ink);
  }
  .cover__title {
    position: absolute;
    top: 118px; left: 0; right: 0;
    text-align: center;
    font-family: "Libre Bodoni", serif;
    font-weight: 500;
    font-size: 104px;
    line-height: 134px;
    letter-spacing: 2px;
    text-transform: uppercase;
    color: var(--title-red);
    background: linear-gradient(180deg, var(--title-red) 0%, var(--title-red-deep) 100%);
    -webkit-background-clip: text;
    background-clip: text;
    -webkit-text-fill-color: transparent;
  }
  .cover__title span { display: block; }
  .cover__genre {
    position: absolute;
    top: 578px; left: 0; right: 0;
    text-align: center;
    font-family: "Libre Bodoni", serif;
    font-size: 25px;
    color: var(--label-ink);
  }
  .cover__imprint {
    position: absolute;
    bottom: 18px; left: 0; right: 0;
    text-align: center;
    font-family: "Libre Bodoni", serif;
    font-size: 25px;
    color: var(--imprint);
  }
</style>
</head>
<body>
  <main class="cover">
    <div class="cover__city" role="img" aria-label="Photographie en noir et blanc d'une ville dense de tours, floutée en traînées verticales vers le haut"></div>
    <p class="cover__author">MATHIS CORVENOT</p>
    <h1 class="cover__title"><span>Watch</span><span>the tide</span><span>turning</span></h1>
    <p class="cover__genre">ROMAN</p>
    <p class="cover__imprint">Editions Murlane</p>
  </main>
</body>
</html>
```